Redesign Website - Current one too plain

The description is in the uploaded file. Please let me know if you need any more information. I'd prefer it if someone could implement the design to a WordPress site but the best design will win, regardless.
I would like the forms to look nice as well
UPDATE:
I don't think we can use the images that I provided, I think they make the site look a bit 'cheap' and I really don't know how to replace them. One thought I have had is to make the "Simple, Unique, Effective" a second feature on the right side of the page with the search on the left
Target Market(s)
Small companies, private sellers of cars and people who rent their caravan/holiday home out
Industry/Entity Type
Advertising
Number of Pages Required
3 page
Colors
Designer to choose colors to be used in the design.
Look and feel
Each slider illustrates characteristics of the customer's brand and the style your logo design should communicate.

```html
<!DOCTYPE html>
<html lang="en">
<head>
<meta charset="UTF-8">
<title>Kodemark – Find them by their code</title>
<link href="https://fonts.googleapis.com/css2?family=Poppins:wght@300;400;500;600;800&display=swap" rel="stylesheet">
<style>
  :root {
    --header-bg: #e0e0df;
    --ink: #000000;
    --text: #1a1a1a;
    --muted-line: #d2d2d2;
    --accent: #e2f51a;
    --panel: #ffffff;
    --silk-light: #f4f4f4;
    --silk-mid: #e6e6e6;
    --silk-dark: #d6d6d6;
    --van-light: #f2f2f2;
    --van-mid: #cfcfcf;
    --van-dark: #3a3a3a;
  }
  * { box-sizing: border-box; margin: 0; padding: 0; }
  html, body { width: 1200px; height: 782px; overflow: hidden; }
  body {
    position: relative;
    font-family: "Poppins", Arial, sans-serif;
    color: var(--text);
    background: var(--panel);
  }
  .page-backdrop {
    position: absolute; left: 0; top: 68px; width: 1200px; height: 681px;
    background:
      radial-gradient(ellipse 700px 180px at 300px 120px, var(--silk-light), transparent 70%),
      radial-gradient(ellipse 600px 160px at 900px 620px, var(--silk-light), transparent 70%),
      linear-gradient(160deg, var(--silk-mid) 0%, var(--silk-light) 35%, var(--silk-dark) 60%, var(--silk-light) 80%, var(--silk-mid) 100%);
  }
  .site-header {
    position: absolute; left: 0; top: 0; width: 1200px; height: 68px;
    background: var(--header-bg);
  }
  .brand {
    position: absolute; left: 93px; top: 22px;
    display: flex; align-items: center; gap: 8px;
    font-size: 19px; font-weight: 400; letter-spacing: 3px; color: var(--ink);
    text-transform: uppercase;
  }
  .brand-dot { width: 14px; height: 14px; border-radius: 50%; background: var(--ink); }
  .main-nav a {
    position: absolute; top: 30px; font-size: 16px; font-weight: 400;
    color: var(--ink); text-decoration: none; line-height: 20px;
  }
  .main-nav .nav-home { left: 599px; }
  .main-nav .nav-advertise { left: 696px; }
  .main-nav .nav-contact { left: 819px; }
  .main-nav .nav-register { left: 932px; }
  .main-nav .nav-login {
    left: 1025px; top: 25px; width: 86px; height: 32px;
    background: var(--ink); color: var(--accent);
    display: flex; align-items: center; justify-content: center;
  }
  .side-rule {
    position: absolute; left: 271px; top: 14px; width: 1px; height: 552px;
    background: var(--muted-line);
  }
  .hero-visual {
    position: absolute; left: 373px; top: 133px; width: 809px; height: 365px;
    border-radius: 120px 60px 30px 20px / 90px 40px 30px 20px;
    background: linear-gradient(180deg, var(--van-light) 0%, var(--van-mid) 65%, var(--van-dark) 100%);
  }
  .code-picker {
    position: absolute; left: 98px; top: 150px; width: 150px; height: 150px;
  }
  .code-picker svg { position: absolute; }
  .code-value {
    position: absolute; left: 0; top: 28px; width: 150px;
    font-size: 120px; font-weight: 800; line-height: 100px; letter-spacing: 2px;
    color: var(--ink);
  }
  .search-bar {
    position: absolute; left: 98px; top: 325px; width: 964px; height: 74px;
    background: var(--panel);
    box-shadow: 0 6px 24px rgba(0,0,0,0.06);
  }
  .search-field {
    position: absolute; top: 21px; height: 29px;
    border-bottom: 1.5px solid #b8b8b8;
    font-size: 13px; color: var(--text);
    display: flex; justify-content: space-between; align-items: center;
  }
  .search-field .radio {
    width: 11px; height: 11px; border: 1px solid #555; border-radius: 50%;
  }
  .field-car { left: 60px; width: 144px; }
  .field-caravan { left: 303px; width: 139px; }
  .field-company { left: 541px; width: 140px; }
  .search-button {
    position: absolute; left: 779px; top: 22px; width: 118px; height: 32px;
    background: var(--ink); color: var(--accent);
    font-size: 13px; display: flex; align-items: center; justify-content: center;
  }
  .feature-strip {
    position: absolute; left: 221px; top: 566px; width: 759px; height: 119px;
    background: var(--panel); display: flex;
  }
  .feature {
    text-align: center; padding-top: 22px;
  }
  .feature + .feature { border-left: 1.5px solid #9a9a9a; }
  .feature { margin: 21px 0; padding-top: 1px; }
  .feature-simple { width: 225px; }
  .feature-unique { width: 263px; }
  .feature-effective { width: 271px; }
  .feature h2 { font-size: 16px; font-weight: 600; color: var(--ink); line-height: 24px; }
  .feature p { margin-top: 10px; font-size: 13px; line-height: 19px; color: var(--text); }
  .site-footer {
    position: absolute; left: 0; top: 749px; width: 1200px; height: 33px;
    border-top: 1px solid #9e9e9e; background: var(--panel);
    font-size: 13px; font-weight: 500; color: var(--ink);
    text-align: center; line-height: 30px;
  }
</style>
</head>
<body>
  <div class="page-backdrop" role="img" aria-label="Soft flowing white silk fabric background"></div>

  <header class="site-header">
    <div class="brand"><span class="brand-dot"></span>Kodemark</div>
    <nav class="main-nav">
      <a class="nav-home" href="#">Home</a>
      <a class="nav-advertise" href="#">Advertise</a>
      <a class="nav-contact" href="#">Contact</a>
      <a class="nav-register" href="#">Register</a>
      <a class="nav-login" href="#">Login</a>
    </nav>
  </header>

  <div class="side-rule" style="top:68px;height:498px;"></div>

  <div class="hero-visual" role="img" aria-label="White panel van with an A1 code sticker on its side"></div>

  <div class="code-picker">
    <svg width="20" height="12" style="left:33px;top:8px" viewBox="0 0 20 12"><path d="M2 10 L10 3 L18 10" fill="none" stroke="#000" stroke-width="2"/></svg>
    <svg width="20" height="12" style="left:112px;top:8px" viewBox="0 0 20 12"><path d="M2 10 L10 3 L18 10" fill="none" stroke="#000" stroke-width="2"/></svg>
    <div class="code-value">A1</div>
    <svg width="20" height="12" style="left:33px;top:138px" viewBox="0 0 20 12"><path d="M2 2 L10 9 L18 2" fill="none" stroke="#000" stroke-width="2"/></svg>
    <svg width="20" height="12" style="left:112px;top:138px" viewBox="0 0 20 12"><path d="M2 2 L10 9 L18 2" fill="none" stroke="#000" stroke-width="2"/></svg>
  </div>

  <form class="search-bar">
    <label class="search-field field-car">Car<span class="radio"></span></label>
    <label class="search-field field-caravan">Caravan<span class="radio"></span></label>
    <label class="search-field field-company">Company<span class="radio"></span></label>
    <div class="search-button">Search</div>
  </form>

  <section class="feature-strip">
    <div class="feature feature-simple">
      <h2>Simple</h2>
      <p>create your advert and<br>display your code</p>
    </div>
    <div class="feature feature-unique">
      <h2>Unique</h2>
      <p>customers find you by an<br>easy-to-remember code</p>
    </div>
    <div class="feature feature-effective">
      <h2>Effective</h2>
      <p>customers are directed to you<br>and not a list of your competitors</p>
    </div>
  </section>

  <footer class="site-footer">© 2023 Kodemark. All rights reserved</footer>
</body>
</html>
```